Meridale Bed Company Needs Business Card

Looking for a very nice looking business card. Creative but not extravagant. We sell beds and pillows across the U.S. and need something professional but catchy. I have attached the logo.

Name : Devin Holt
Title : President
Phone : (800) 471-2960
Email: sleep@quilmora.com
Website: www.quilmora.com

Can be single-sided or double-sided
horizontal or vertical

Can use Blues/Greys

Target Market(s)

Mass Market

Industry/Entity Type

Retail

Contact Information for Business Card

Name : Devin Holt
Title : President
Phone : (800) 471-2960
Email: sleep@quilmora.com
Website: www.quilmora.com

Requirements
Must have
• Clean, Modern, Smooth
• Can use Blues/Greys
• On the other side without the information - have something simple like www.quilmora.com or our logo
Nice to have
• Surprise me
Should not have
• Nothing crazy, nothing cluttered

```html
<!DOCTYPE html>
<html lang="en">
<head>
<meta charset="utf-8">
<title>Quilmora Business Card</title>
<link rel="stylesheet" href="https://fonts.googleapis.com/css2?family=Open+Sans:wght@300;400;600;700&display=swap">
<style>
  :root {
    --page-bg: #e9ebee;
    --card-white: #ffffff;
    --card-shade: #eef0f2;
    --brand-blue: #36a6de;
    --brand-blue-deep: #2489c2;
    --text-grey: #555a60;
    --band-grey: #6d7176;
  }
  * { box-sizing: border-box; margin: 0; padding: 0; }
  html, body {
    width: 1200px; height: 843px; overflow: hidden;
    background: var(--page-bg);
    font-family: "Open Sans", Arial, sans-serif;
  }
  .canvas {
    width: 1200px; height: 843px;
    display: flex; flex-direction: column; align-items: center; justify-content: center;
    gap: 56px;
  }
  .card {
    position: relative;
    width: 600px; height: 343px;
    border-radius: 3px;
    overflow: hidden;
    box-shadow: 0 6px 18px rgba(0,0,0,0.15);
  }
  /* Back side */
  .card-back {
    background: linear-gradient(160deg, var(--brand-blue) 0%, var(--brand-blue-deep) 100%);
    display: flex; flex-direction: column; align-items: center; justify-content: center;
  }
  .card-back .wordmark { color: #ffffff; font-size: 70px; }
  .card-back .back-url {
    margin-top: 10px;
    color: rgba(255,255,255,0.85);
    font-size: 11px; letter-spacing: 6px;
  }
  .wordmark {
    font-family: "Open Sans", Arial, sans-serif;
    font-weight: 300;
    letter-spacing: 1px;
    line-height: 1;
  }
  /* Front side */
  .card-front {
    background: linear-gradient(160deg, var(--card-white) 45%, var(--card-shade) 100%);
  }
  .card-front .wordmark {
    position: absolute; top: 62px; right: 40px;
    color: var(--brand-blue); font-size: 66px;
  }
  .contact-block {
    position: absolute; left: 40px; top: 176px;
  }
  .person-name {
    color: var(--brand-blue); font-weight: 700; font-size: 19px; line-height: 1.2;
  }
  .person-title {
    color: var(--text-grey); font-size: 15px; margin-bottom: 10px;
  }
  .contact-list { list-style: none; }
  .contact-list li {
    display: flex; align-items: center; gap: 9px;
    color: var(--text-grey); font-size: 15px; line-height: 24px;
  }
  .contact-list svg { width: 14px; height: 14px; flex: none; }
  .edge-band {
    position: absolute; left: 0; bottom: 0; width: 600px; height: 16px;
  }
</style>
</head>
<body>
<main class="canvas">
  <section class="card card-back" aria-label="Card back">
    <div class="wordmark">quilmora</div>
    <div class="back-url">www.quilmora.com</div>
  </section>

  <section class="card card-front" aria-label="Card front">
    <div class="wordmark">quilmora</div>
    <div class="contact-block">
      <p class="person-name">Devin Holt</p>
      <p class="person-title">President</p>
      <ul class="contact-list">
        <li>
          <svg viewBox="0 0 14 14" aria-hidden="true"><path fill="var(--brand-blue)" d="M3 1.5l2 2.2-1.1 1.6a7 7 0 0 0 4.8 4.8l1.6-1.1 2.2 2-1.3 1.8C6.4 12.6 1.4 7.6 1.2 2.8z"/></svg>
          <span>(800) 471-2960</span>
        </li>
        <li>
          <svg viewBox="0 0 14 14" aria-hidden="true"><rect x="1" y="3" width="12" height="8.5" rx="1" fill="var(--brand-blue)"/><path d="M1.5 3.5L7 8l5.5-4.5" fill="none" stroke="#fff" stroke-width="1"/></svg>
          <span>sleep@quilmora.com</span>
        </li>
        <li>
          <svg viewBox="0 0 14 14" aria-hidden="true"><circle cx="7" cy="7" r="6" fill="var(--brand-blue)"/><ellipse cx="7" cy="7" rx="2.6" ry="6" fill="none" stroke="#fff" stroke-width="0.9"/><path d="M1 7h12" stroke="#fff" stroke-width="0.9"/></svg>
          <span>www.quilmora.com</span>
        </li>
      </ul>
    </div>
    <svg class="edge-band" viewBox="0 0 600 16" preserveAspectRatio="none" aria-hidden="true">
      <polygon points="0,0 380,0 373,16 0,16" fill="var(--brand-blue)"/>
      <polygon points="383,0 600,0 600,16 376,16" fill="var(--band-grey)"/>
    </svg>
  </section>
</main>
</body>
</html>
```